Business Cards for new orthopaedic surgery practice

My husband and I are starting our own orthopaedic surgery practice. We are looking for a business card that is uniform, but one will have my name/title and the other will have his. You can just create one design with my name on it for now. But when I choose your design as the winning design I will ask that you add another copy with his name/title.

We are looking for classy, simple, elite all in one. We like dark blues/a little gold/yellow. Something that goes with our logo. We want our logo incorporated. Here is all the info you need:
Business name: RV Bone & Vitality Center
Location: 38517 North Willowmere Ave
Maple Harbor, FL 33990
Phone: 954-218-4063
Fax: 954-582-7341
Email: info@myrvbonecare.example

Names: Lydia Vance, M.D.
Board Certified Hand and Upper Extremity Surgeon

Ebo Dansu, M.D.
Board Certified Hip & Knee Replacement/General Orthopaedic Surgeon

Can decide what you want to put on the back. Maybe a slogan:
Steady Hands. Lasting Strength

I am just going to upload our logo. The only thing is if we select you as the winning design, the location, and phone numbers may change. We will need your help to update that once fully solidified.

Industry/Entity Type

Medical

Contact Information for Business Card

Colors
0054AA
0677BA
7BADD7
CADEEF
E8F1F8
0094D4
00A9DD
6FCCEA
C7EBF8
E9F6FB

Requirements
Must have
• class, appeal,
Should not have
• We want to air on the side of masculine if we are looking at masculine vs. feminine feel. But we still want it classy, sophisticated, and something we will love

```html
<!DOCTYPE html>
<html lang="en">
<head>
<meta charset="utf-8">
<title>RV Bone &amp; Vitality Center – Business Card</title>
<link href="https://fonts.googleapis.com/css2?family=Marcellus&family=Montserrat:wght@500;600;700&family=Merriweather:wght@700&display=swap" rel="stylesheet">
<style>
  :root{
    --stage:#2a2a2c;
    --navy:#283579;
    --navy-deep:#222d6b;
    --gold:#d8a93f;
    --gold-light:#f3d27a;
    --gold-dark:#b8862c;
    --cyan:#17b8e6;
    --white:#ffffff;
  }
  *{box-sizing:border-box;margin:0;padding:0}
  html,body{width:1200px;height:694px;overflow:hidden;background:var(--stage)}
  .stage{position:relative;width:1200px;height:694px;display:flex;align-items:center;justify-content:center;gap:40px}
  .card{position:relative;width:540px;height:309px;border-radius:18px;overflow:hidden;background:linear-gradient(135deg,var(--navy) 0%,var(--navy-deep) 100%);box-shadow:0 14px 30px rgba(0,0,0,.45)}

  /* Front */
  .front{display:flex;align-items:center;justify-content:center}
  .brand-lockup{display:flex;align-items:center;gap:14px}
  .brand-dot{width:16px;height:16px;border-radius:50%;background:var(--gold)}
  .brand-name{font-family:"Marcellus",serif;font-weight:400;color:var(--gold);font-size:32px;letter-spacing:1.5px;text-transform:uppercase;line-height:1.15}

  /* Back */
  .back-lockup{position:absolute;left:30px;top:40px;display:flex;align-items:center;gap:10px}
  .back-lockup .brand-dot{width:12px;height:12px}
  .brand-name--small{font-family:"Marcellus",serif;font-weight:400;color:var(--gold);font-size:17px;letter-spacing:1px;text-transform:uppercase;line-height:1.2}
  .person{position:absolute;right:28px;top:36px;text-align:right}
  .person-name{font-family:"Montserrat",sans-serif;font-weight:700;color:var(--gold);font-size:19px;letter-spacing:.5px}
  .person-title{font-family:"Montserrat",sans-serif;font-weight:600;color:var(--white);font-size:11px;margin-top:4px}
  .address{position:absolute;right:28px;top:146px;text-align:right;font-family:"Montserrat",sans-serif;font-weight:500;color:var(--white);font-size:12.5px;line-height:1.6}
  .contacts{position:absolute;left:30px;top:150px;list-style:none;font-family:"Montserrat",sans-serif;font-weight:500;color:var(--white);font-size:12.5px}
  .contacts li{display:flex;align-items:center;gap:8px;height:20px}
  .contacts svg{width:12px;height:12px;fill:var(--cyan)}
  .band{position:absolute;left:0;bottom:0;width:540px;height:309px;pointer-events:none}
  .slogan{position:absolute;left:30px;bottom:12px;font-family:"Merriweather",serif;font-weight:700;color:var(--navy-deep);font-size:12px;letter-spacing:.3px}
</style>
</head>
<body>
<main class="stage">
  <section class="card front" aria-label="Card front">
    <div class="brand-lockup">
      <span class="brand-dot"></span>
      <span class="brand-name">RV Bone &amp;<br>Vitality Center</span>
    </div>
  </section>

  <section class="card back" aria-label="Card back">
    <svg class="band" viewBox="0 0 540 309" aria-hidden="true">
      <defs>
        <linearGradient id="goldBand" x1="0" y1="0" x2="1" y2="0">
          <stop offset="0" stop-color="#b8862c"/>
          <stop offset=".5" stop-color="#f3d27a"/>
          <stop offset="1" stop-color="#d8a93f"/>
        </linearGradient>
      </defs>
      <path d="M345 238 H540 V250 H345 Q338 250 334 244 Z" fill="#17b8e6"/>
      <path d="M0 270 H320 Q330 270 336 258 Q340 252 350 252 H540 V309 H0 Z" fill="url(#goldBand)"/>
    </svg>

    <div class="back-lockup">
      <span class="brand-dot"></span>
      <span class="brand-name--small">RV Bone &amp;<br>Vitality Center</span>
    </div>

    <div class="person">
      <p class="person-name">LYDIA VANCE, M.D</p>
      <p class="person-title">Hand and Upper Extremity Surgery</p>
    </div>

    <p class="address">38517 North Willowmere Ave<br>Maple Harbor, FL 33990</p>

    <ul class="contacts">
      <li><svg viewBox="0 0 24 24"><path d="M6.6 10.8a15.1 15.1 0 0 0 6.6 6.6l2.2-2.2a1 1 0 0 1 1-.25 11.4 11.4 0 0 0 3.6.57 1 1 0 0 1 1 1V20a1 1 0 0 1-1 1A17 17 0 0 1 3 4a1 1 0 0 1 1-1h3.5a1 1 0 0 1 1 1c0 1.25.2 2.45.57 3.57a1 1 0 0 1-.25 1z"/></svg>954-218-4063</li>
      <li><svg viewBox="0 0 24 24"><path d="M6 2h12v6H6zM3 9h18a1 1 0 0 1 1 1v7h-4v5H6v-5H2v-7a1 1 0 0 1 1-1zm5 8v3h8v-3z"/></svg>954-582-7341</li>
      <li><svg viewBox="0 0 24 24"><path d="M2 5h20v14H2zm2 2v.5l8 5 8-5V7z"/></svg>info@myrvbonecare.example</li>
      <li><svg viewBox="0 0 24 24"><path d="M12 2a10 10 0 1 0 0 20 10 10 0 0 0 0-20zm0 2c1.2 0 2.6 2.2 3 6H9c.4-3.8 1.8-6 3-6zm-3 8h6c-.3 4-1.8 8-3 8s-2.7-4-3-8zm-5 0h3c.1 2.5.7 4.9 1.6 6.6A8 8 0 0 1 4 12zm13 0h3a8 8 0 0 1-4.6 6.6c.9-1.7 1.5-4.1 1.6-6.6z"/></svg>www.myrvbonecare.example</li>
    </ul>

    <p class="slogan">Steady Hands. Lasting Strength</p>
  </section>
</main>
</body>
</html>
```